Willow Fen Racquet Club (Tennis Country Club)

Racquet and Tennis Country Club in Florida.
This web sight is needed for a Privet Tennis club located in Deerfield Beach city in Florida, USA.
We have 10 clay tennis courts and 2 hard tennis courts, small and cozy swimming pool and a clubhouse (see attached pictures) Attached pictures are for information only because we are under a reconstruction.
Updates

I haven't received any source files and web converted files neither!

Target Market(s)

Adult members, Kids members, Tennis players

Coding

Coded - Design and coding required

Number of Pages Required

3 page

Requirements
Must have
• Logo colors (see attached file)

```html
<!DOCTYPE html>
<html lang="en">
<head>
<meta charset="utf-8">
<title>Willow Fen Racquet Club</title>
<link href="https://fonts.googleapis.com/css2?family=Poppins:wght@300;400;500;600&display=swap" rel="stylesheet">
<style>
:root{
  --green:#0f5a2e;
  --green-dark:#0c4524;
  --band:#0e4a27;
  --ink:#222;
  --muted:#777;
  --mist:#eef0f0;
  --footer:#3a3a3a;
  --white:#fff;
}
*{margin:0;padding:0;box-sizing:border-box}
html,body{width:1200px;height:3315px;overflow:hidden}
body{position:relative;font-family:"Poppins",Arial,sans-serif;color:var(--ink);background:var(--white)}
.abs{position:absolute}
.btn{position:absolute;display:flex;align-items:center;justify-content:center;background:var(--green);color:var(--white);font-size:14px;font-weight:500;letter-spacing:.5px;text-transform:uppercase;border-radius:3px}
.copy{position:absolute;font-size:12.5px;line-height:26px;color:var(--muted)}

/* header */
.site-header{position:absolute;left:0;top:0;width:1200px;height:88px;background:var(--white);border-top:5px solid var(--green);z-index:3}
.brand-disc{position:absolute;left:86px;top:-20px;width:186px;height:192px;border-radius:50%;background:var(--white);z-index:4;display:flex;align-items:center;justify-content:center}
.brand-disc span{font-size:26px;font-weight:600;color:var(--green-dark);text-align:center;line-height:30px;margin-top:30px}
.nav{position:absolute;top:36px;font-size:13.5px;font-weight:500;color:#222;text-transform:uppercase}
.search{position:absolute;left:1066px;top:21px;width:48px;height:48px;border:2px solid var(--green);border-radius:50%}

/* hero */
.hero{position:absolute;left:0;top:88px;width:1200px;height:568px;background:linear-gradient(180deg,#1f5a3a 0%,#2c5f41 18%,#8a3d22 40%,#b8562e 65%,#c9673a 100%)}
.hero-panel{position:absolute;left:643px;top:265px;width:470px;height:225px;background:rgba(60,35,25,.62)}
.hero-title{position:absolute;left:643px;top:292px;width:470px;text-align:center;font-size:40px;font-weight:500;color:var(--white)}
.hero-text{position:absolute;left:665px;top:360px;width:426px;text-align:center;font-size:11.5px;line-height:26px;color:#eee}

/* welcome */
.welcome-title{position:absolute;left:0;top:708px;width:1200px;text-align:center;font-size:30px;font-weight:400;color:var(--green)}
.welcome-title b{font-weight:600}

/* features */
.features{position:absolute;left:0;top:988px;width:1200px;height:917px;background:linear-gradient(180deg,#f4f5f5,#e7eaea)}
.photo{position:absolute;border-radius:50%;border:8px solid var(--white);box-shadow:0 4px 14px rgba(0,0,0,.25)}
.feat-title{position:absolute;font-size:29px;font-weight:400;color:var(--green)}
.feat-title b{font-weight:600}
.dot{position:absolute;width:18px;height:18px;border-radius:50%;background:var(--green)}

/* band */
.band{position:absolute;left:0;top:1905px;width:1200px;height:371px;background:radial-gradient(ellipse at 40% 40%,#1b5a33,var(--band) 70%)}
.band-head{position:absolute;left:0;top:2022px;width:1200px;text-align:center;font-size:23px;font-weight:500;color:var(--white);text-transform:uppercase}
.band-sub{position:absolute;left:0;top:2066px;width:1200px;text-align:center;font-size:21px;font-weight:300;color:var(--white)}
.btn-ghost{position:absolute;left:466px;top:2126px;width:265px;height:53px;border:2px solid var(--white);border-radius:27px;color:var(--white);font-size:14px;font-weight:500;display:flex;align-items:center;justify-content:center;text-transform:uppercase}

/* columns */
.col-title{position:absolute;width:360px;text-align:center;font-size:24px;font-weight:500;color:var(--green);text-transform:uppercase}
.col-copy{position:absolute;width:290px;text-align:center;font-size:12px;line-height:26px;color:var(--muted)}
.col-brand{position:absolute;left:519px;top:2320px;width:160px;text-align:center}
.col-brand i{display:block;width:20px;height:20px;border-radius:50%;background:var(--green);margin:0 auto 8px}
.col-brand span{font-size:24px;font-weight:600;color:var(--green-dark)}

/* footer */
.site-footer{position:absolute;left:0;top:2979px;width:1200px;height:336px;background:var(--footer);color:var(--white)}
.foot-brand{position:absolute;left:100px;top:3120px;width:300px;text-align:center;font-size:38px;font-weight:500;color:var(--white);line-height:44px}
.foot-ring{position:absolute;left:198px;top:3032px;width:100px;height:100px;border-radius:50%;border:5px solid var(--white)}
.foot-h{position:absolute;top:3010px;font-size:16px;font-weight:500;text-transform:uppercase}
.foot-t{position:absolute;font-size:12px;line-height:24px;color:#eee}
.email{position:absolute;left:769px;top:3094px;width:294px;height:44px;background:var(--white);color:#666;font-size:12px;padding-left:18px;display:flex;align-items:center}
.send{position:absolute;left:1063px;top:3094px;width:44px;height:44px;background:var(--green)}
.social{position:absolute;top:3173px;width:36px;height:36px;border:2px solid var(--white);border-radius:50%}
.copyright{position:absolute;left:0;top:3273px;width:1200px;text-align:center;font-size:12px;color:#ddd}
</style>
</head>
<body>

<header class="site-header">
  <div class="nav" style="left:592px">Home</div>
  <div class="nav" style="left:676px">About Us</div>
  <div class="nav" style="left:785px">Services</div>
  <div class="nav" style="left:891px">News</div>
  <div class="nav" style="left:973px">Contact Us</div>
  <div class="search">
    <svg width="44" height="44" viewBox="0 0 44 44"><circle cx="21" cy="21" r="5" fill="none" stroke="#222" stroke-width="2"/><line x1="25" y1="25" x2="29" y2="29" stroke="#222" stroke-width="2.4"/></svg>
  </div>
</header>
<div class="brand-disc"><span>Willow Fen</span></div>

<section class="hero" role="img" aria-label="Photo of tennis players rallying on a red clay court"></section>
<div class="hero-panel"></div>
<h1 class="hero-title">Willow Fen</h1>
<p class="hero-text">Sed ut perspiciatis unde omnis iste natus error sit voluptatem accusantium doloremque laudantium, totam rem aperiam, eaque ipsa quae ab illo inventore veritatis et quasi architecto beatae vitae dicta sunt explicabo.</p>
<div class="btn" style="left:791px;top:466px;width:173px;height:47px">Read More</div>

<h2 class="welcome-title">Welcome to <b>Willow Fen</b></h2>
<p class="copy" style="left:261px;top:770px;width:678px;text-align:center">Sed ut perspiciatis unde omnis iste natus error sit voluptatem accusantium doloremque laudantium, totam rem aperiam, eaque ipsa quae ab illo inventore veritatis et quasi architecto beatae vitae dicta sunt explicabo. Nemo enim ipsam voluptatem quia voluptas sit aspernatur aut odit aut fugit, sed quia consequuntur magni dolores eos qui ratione voluptatem sequi nesciunt.</p>
<div class="btn" style="left:491px;top:884px;width:216px;height:46px;font-size:15px">Get In Touch</div>

<section class="features" role="img" aria-label="Faint sketch of the clubhouse building"></section>
<div class="photo" role="img" aria-label="Photo of the swimming pool" style="left:148px;top:1032px;width:278px;height:278px;background:linear-gradient(160deg,#3c6b3e 0%,#3a86c4 35%,#1f5fa8 100%)"></div>
<h2 class="feat-title" style="left:502px;top:1052px">Swimming <b>Pool</b></h2>
<p class="copy" style="left:502px;top:1114px;width:540px">Sed ut perspiciatis unde omnis iste natus error sit voluptatem accusantium doloremque laudantium, totam rem aperiam, eaque ipsa quae ab illo inventore veritatis et quasi architecto beatae vitae dicta sunt explicabo. Nemo enim ipsam voluptatem quia voluptas sit aspernatur aut odit aut fugit, sed quia consequuntur magni dolores eos qui ratione voluptatem sequi nesciunt.</p>
<div class="btn" style="left:502px;top:1246px;width:176px;height:45px;font-size:13px">Read More</div>

<div class="dot" style="left:278px;top:1326px"></div>
<svg class="abs" style="left:0;top:0" width="1200" height="1530" viewBox="0 0 1200 1530">
  <path d="M287 1344 V1441 H903 V1516" fill="none" stroke="#777" stroke-width="1.5" stroke-dasharray="4 4"/>
</svg>
<div class="dot" style="left:894px;top:1516px"></div>

<h2 class="feat-title" style="left:148px;top:1570px"><span>Club</span><b>House</b></h2>
<p class="copy" style="left:148px;top:1633px;width:540px">Sed ut perspiciatis unde omnis iste natus error sit voluptatem accusantium doloremque laudantium, totam rem aperiam, eaque ipsa quae ab illo inventore veritatis et quasi architecto beatae vitae dicta sunt explicabo. Nemo enim ipsam voluptatem quia voluptas sit aspernatur aut odit aut fugit, sed quia consequuntur magni dolores eos qui ratione voluptatem sequi nesciunt.</p>
<div class="btn" style="left:148px;top:1768px;width:177px;height:44px;font-size:13px">Read More</div>
<div class="photo" role="img" aria-label="Photo of the tennis courts beside the clubhouse under a blue sky" style="left:780px;top:1547px;width:278px;height:278px;background:linear-gradient(180deg,#5f8fd0 0%,#9bb8dc 40%,#3c6f5a 70%,#2b5a7a 100%)"></div>

<section class="band" role="img" aria-label="Dark green tinted photo of palm trees"></section>
<h2 class="band-head">Sed ut perspiciatis unde omnis iste natus error sit voluptatem</h2>
<p class="band-sub">loremque laudantium, totam rem aperiam eaque ipsa</p>
<div class="btn-ghost">Click Here For More Info</div>

<h3 class="col-title" style="left:59px;top:2336px">About Us</h3>
<p class="col-copy" style="left:94px;top:2386px">Sed ut perspiciatis unde omnis iste natus error sit voluptatem accusantium doloremque laudantium vitae dicta sunt explicabo.</p>
<div class="photo" role="img" aria-label="Rendering of the new clubhouse exterior" style="left:100px;top:2489px;width:278px;height:278px;background:linear-gradient(180deg,#f2f2f2 0%,#dcdcdc 55%,#4a4a4a 100%)"></div>
<div class="btn" style="left:144px;top:2796px;width:192px;height:44px;font-size:13px">Learn More</div>

<div class="col-brand"><i></i><span>Willow Fen</span></div>
<h3 class="col-title" style="left:419px;top:2430px">Tennis Court</h3>
<p class="col-copy" style="left:454px;top:2474px">Sed ut perspiciatis unde omnis iste natus error sit voluptatem accusantium doloremque laudantium vitae dicta sunt explicabo.</p>
<div class="photo" role="img" aria-label="Photo of hard tennis courts with floodlights" style="left:460px;top:2577px;width:278px;height:278px;background:linear-gradient(180deg,#5f8fd0 0%,#a8c0de 42%,#3c6f5a 68%,#2b5a7a 100%)"></div>
<div class="btn" style="left:506px;top:2882px;width:194px;height:46px;font-size:13px">Learn More</div>

<h3 class="col-title" style="left:783px;top:2336px">Clay Tennis</h3>
<p class="col-copy" style="left:818px;top:2386px">Sed ut perspiciatis unde omnis iste natus error sit voluptatem accusantium doloremque laudantium vitae dicta sunt explicabo.</p>
<div class="photo" role="img" aria-label="Rendering of a covered pavilion next to the clay courts" style="left:824px;top:2489px;width:278px;height:278px;background:linear-gradient(160deg,#e8e8e8 0%,#bdbdbd 50%,#6b4a36 100%)"></div>
<div class="btn" style="left:868px;top:2796px;width:195px;height:44px;font-size:13px">Learn More</div>

<footer class="site-footer"></footer>
<div class="foot-ring"></div>
<div class="foot-brand">Willow Fen</div>

<div class="foot-h" style="left:469px">Contact Us</div>
<svg class="abs" style="left:472px;top:3056px" width="18" height="22" viewBox="0 0 18 22"><path d="M9 1a7 7 0 0 1 7 7c0 5-7 13-7 13S2 13 2 8a7 7 0 0 1 7-7z" fill="#fff"/><circle cx="9" cy="8" r="2.6" fill="#3a3a3a"/></svg>
<p class="foot-t" style="left:506px;top:3050px">Willow Fen<br># 254 Lorem Ipsum Dummy Text<br>Lorem Ipsum Dummy</p>
<svg class="abs" style="left:472px;top:3148px" width="18" height="18" viewBox="0 0 24 24"><path d="M6.6 10.8a15 15 0 0 0 6.6 6.6l2.2-2.2c.3-.3.7-.4 1-.2 1.1.4 2.3.6 3.6.6.6 0 1 .4 1 1V20c0 .6-.4 1-1 1A17 17 0 0 1 3 4c0-.6.4-1 1-1h3.5c.6 0 1 .4 1 1 0 1.3.2 2.5.6 3.6.1.3 0 .7-.2 1z" fill="#fff"/></svg>
<p class="foot-t" style="left:506px;top:3146px">Telephone : (000)-121-1231<br>Fax : (000)-121-1231</p>

<div class="foot-h" style="left:769px">Newsletter</div>
<p class="foot-t" style="left:769px;top:3054px">Sed ut perspiciatis unde omnis iste natus error sit</p>
<div class="email">Enter Your Email Id :</div>
<div class="send"><svg width="44" height="44" viewBox="0 0 44 44"><path d="M13 22l18-8-6 17-3-7z" fill="#fff"/></svg></div>
<div class="social" style="left:842px"></div>
<div class="social" style="left:884px"></div>
<div class="social" style="left:926px"></div>
<div class="social" style="left:968px"></div>
<div class="social" style="left:1010px"></div>

<p class="copyright">© Copyright -2018 Willow Fen. All rights reserved.</p>

</body>
</html>
```